Web Design Project

The aim of this project to design a website for a service that would offer services for small business and non profit organizations using opensource software that is weaved to work together in harmony.

The website name is: vestolia.net

Vestolia in Arabic means: cabbage. Cabbage is composed of leaves, actually there is nothing except leaves. Each leave by itself is not called cabbage, but a collection of leaves that are organized in a central way would give us cabbage.

Same idea for Vestolia where open source software very well organized and integrated would create a new thing with a new value.

Target Market(s)

Small business, Europe, Africa, Far east and Middle east

Industry/Entity Type

Small Business

Requirements
Must have
• The website would offer the following sections:
* Home page
* Benefits: value of vestolia
* Applications: applications offered by vestolia
* Pricing
* Purchase
* Customer log in
* Support
- FAQ
- Knowledge base
- Forums
- Open tickets

Please take the following consideration in design:
* White should predominate
* Only black and the colors of logo are permitted (attched)
Nice to have
• Design is better to express:
* Openness
* Dynamic
* Usable
* Cost effective

```html
<!DOCTYPE html>
<html lang="en">
<head>
<meta charset="utf-8">
<title>Vestolia</title>
<link href="https://fonts.googleapis.com/css2?family=Questrial&family=Oswald:wght@500&family=Open+Sans:wght@400;600;700&display=swap" rel="stylesheet">
<style>
:root{
  --green:#8cc63f;
  --blue:#0a8fd8;
  --yellow:#f5c000;
  --magenta:#b34d8c;
  --ink:#222;
  --taupe:#8a7f75;
  --text:#555;
  --field:#f4f4f4;
  --field-line:#cfcfcf;
  --footer:#5f5f5f;
}
*{margin:0;padding:0;box-sizing:border-box}
html,body{width:1040px;height:1200px;overflow:hidden;background:#fff}
body{position:relative;font-family:"Open Sans",Arial,sans-serif;color:var(--text)}
.abs{position:absolute}

.brand{left:20px;top:38px;display:flex;align-items:center;gap:12px}
.brand-dot{width:40px;height:40px;border-radius:50%;background:var(--green)}
.brand-name{font-family:"Questrial",sans-serif;font-size:36px;color:var(--ink);line-height:1}

.utility{right:22px;top:16px;display:flex;gap:12px;font-family:Arial,sans-serif;font-size:12px;color:#222}
.utility a{display:flex;flex-direction:column;align-items:center;gap:3px;color:inherit;text-decoration:none}
.utility svg{width:18px;height:16px}

.tagline{right:26px;top:66px;font-family:"Questrial",sans-serif;font-size:28px;color:#222}

.nav{left:0;top:118px;width:1040px;height:30px;background:var(--green);display:flex}
.nav a{color:#fff;text-decoration:none;font-family:"Questrial",sans-serif;font-weight:700;font-size:17px;line-height:30px;text-align:center;letter-spacing:.2px}
.nav a.active{background:var(--blue)}

.hero{left:0;top:148px;width:1040px;height:376px;
  background:radial-gradient(circle at 40% 55%,#e8f2ff 0,#9fb8d8 18%,transparent 40%),
             radial-gradient(circle at 78% 40%,#f4fbff 0,#b9d6ef 12%,transparent 30%),
             linear-gradient(90deg,#7b92b2 0%,#4d5f80 25%,#3b4b6a 45%,#7d9bc4 70%,#a7c2e0 100%)}

.band{left:0;top:524px;width:1040px;height:260px;background:linear-gradient(#e6f2f8,#fff)}

.card{top:573px;width:319px;height:190px;color:#fff;padding:22px 14px 0;overflow:hidden}
.card h2{font-family:"Oswald",sans-serif;font-weight:500;font-size:27px;line-height:1.1;text-transform:uppercase;letter-spacing:-.3px;position:relative}
.card p{font-size:12.5px;line-height:15.5px;margin-top:8px;position:relative}
.card .more{position:absolute;left:13px;top:137px;width:100px;height:26px;border-radius:13px;background:#fff;border:2px solid #ddd;font-size:9.5px;font-weight:700;color:#666;text-align:center;line-height:22px;text-transform:uppercase}
.card .deco{position:absolute;right:14px;top:12px;width:80px;height:80px;opacity:.35}
.card.support{left:17px;background:var(--yellow)}
.card.apps{left:360px;background:var(--blue)}
.card.kb{left:699px;background:var(--magenta)}

.col{top:823px;width:323px}
.hatch{height:6px;background:repeating-linear-gradient(135deg,#d8d4cf 0 2px,transparent 2px 5px)}
.col-head{display:flex;align-items:center;gap:18px;height:52px;border-bottom:1px solid #cfc9c2}
.col-head svg{width:28px;height:28px;flex:none}
.col-head h3{font-family:"Questrial",sans-serif;font-weight:400;font-size:25px;color:var(--taupe);letter-spacing:.5px}

.contact{left:13px}
.field{width:297px;height:30px;margin-top:0;border:1px solid var(--field-line);border-radius:5px;background:var(--field);font-size:12.5px;color:#444;padding:6px 12px}
.send{width:76px;height:26px;border-radius:13px;background:var(--green);border:2px solid #b8de87;color:#fff;font-size:10px;font-weight:700;text-align:center;line-height:22px}

.news{left:358px}
.item{display:flex;gap:16px;margin-top:33px}
.item+.item{margin-top:33px}
.thumb{width:70px;height:70px;border:1px solid #ddd;padding:3px;flex:none}
.thumb div{width:100%;height:100%}
.item h4{color:var(--blue);font-size:14px;font-weight:700}
.item p{font-size:12.5px;line-height:15px;margin-top:4px}

.testi{left:698px}
.quote{position:relative;padding:32px 10px 0 34px;font-size:12.5px;line-height:15.5px}
.quote .mark{position:absolute;left:4px;top:16px;font-family:Georgia,serif;font-size:86px;color:#e3e8ef;line-height:1}
.quote p{position:relative}
.quote p+p{margin-top:14px}
.quote .who{color:var(--blue);font-weight:700;margin-top:14px}

.footer{left:0;top:1150px;width:1040px;height:28px;background:var(--footer);color:#fff;font-size:11.5px;line-height:28px;text-align:center}
.footer span{margin:0 14px}
</style>
</head>
<body>

<div class="abs brand"><div class="brand-dot"></div><div class="brand-name">vestolia</div></div>

<div class="abs utility">
  <a href="#"><svg viewBox="0 0 18 16"><rect x="3" y="3" width="12" height="8" fill="#444"/><rect x="1" y="12" width="16" height="2" fill="#444"/></svg>login</a>
  <a href="#"><svg viewBox="0 0 18 16"><circle cx="9" cy="5" r="4" fill="#444"/><path d="M2 16c0-4 3-6 7-6s7 2 7 6z" fill="#444"/></svg>support</a>
  <a href="#"><svg viewBox="0 0 18 16"><text x="9" y="14" text-anchor="middle" font-family="Arial" font-weight="700" font-size="15" fill="#444">?</text></svg>FAQ</a>
</div>

<div class="abs tagline">Creating a new thing with a new value</div>

<nav class="abs nav">
  <a class="active" href="#" style="width:127px">home</a>
  <a href="#" style="width:106px">benefits</a>
  <a href="#" style="width:126px">applications</a>
  <a href="#" style="width:94px">pricing</a>
  <a href="#" style="width:122px">purchase</a>
  <a href="#" style="width:180px">knowledge base</a>
  <a href="#" style="width:130px">open tickets</a>
</nav>

<div class="abs hero" role="img" aria-label="Business person touching a glowing digital network interface"></div>

<div class="abs band"></div>

<section class="abs card support">
  <svg class="deco" viewBox="0 0 80 80"><circle cx="40" cy="40" r="34" fill="none" stroke="#fff" stroke-width="8"/><text x="40" y="50" text-anchor="middle" font-family="Oswald" font-size="28" fill="#fff">24</text></svg>
  <h2>24/7 Client Support</h2>
  <p>Lorem ipsum dolor sit amet, consectetuer adipiscing elit, sed diam nonummy nibh euismod tincidunt ut laoreet dolore magna.</p>
  <div class="more">Read more</div>
</section>
<section class="abs card apps">
  <svg class="deco" viewBox="0 0 80 80"><path d="M12 68 L66 14 M14 14 L66 66" stroke="#fff" stroke-width="9" stroke-linecap="round"/></svg>
  <h2>Applications</h2>
  <p>Duis autem vel eum iriure dolor in hendrerit in vulputate velit esse molestie consequat, vel illum dolore eu feugiat nulla facilisis at vero eros.</p>
  <div class="more">Read more</div>
</section>
<section class="abs card kb">
  <svg class="deco" viewBox="0 0 80 80"><circle cx="40" cy="40" r="36" fill="#fff"/></svg>
  <h2>Knowledge Base</h2>
  <p>Ut wisi enim ad minim veniam, quis nostrud exerci tation ullamcorper suscipit lobortis nisl ut aliquip ex ea commodo consequat.</p>
  <div class="more">Read more</div>
</section>

<section class="abs col contact">
  <div class="hatch"></div>
  <div class="col-head">
    <svg viewBox="0 0 28 28"><circle cx="14" cy="9" r="6" fill="#8a7f75"/><path d="M3 28c0-7 5-10 11-10s11 3 11 10z" fill="#8a7f75"/></svg>
    <h3>CONTACT US</h3>
  </div>
  <div class="field" style="margin-top:32px">Full Name</div>
  <div class="field" style="margin-top:6px">Email Address</div>
  <div class="field" style="margin-top:6px;height:71px">Message</div>
  <div class="send" style="margin-top:13px">SEND</div>
</section>

<section class="abs col news">
  <div class="hatch"></div>
  <div class="col-head">
    <svg viewBox="0 0 28 28"><rect x="3" y="5" width="22" height="20" rx="2" fill="none" stroke="#8a7f75" stroke-width="2.5"/><rect x="3" y="5" width="22" height="6" fill="#8a7f75"/><text x="14" y="22" text-anchor="middle" font-family="Arial" font-size="9" font-weight="700" fill="#8a7f75">15</text></svg>
    <h3>LATEST NEWS</h3>
  </div>
  <div class="item">
    <div class="thumb"><div role="img" aria-label="Green arrow graphic" style="background:linear-gradient(135deg,#d9ead0,#7cbf4a)"></div></div>
    <div><h4>Fri, January. 03</h4><p>Lorem ipsum dolor sit amet, consectet adipiscing elit, sed diam nonummy nibh euismod tincidunt ut .</p></div>
  </div>
  <div class="item">
    <div class="thumb"><div role="img" aria-label="Blue globe graphic" style="background:linear-gradient(135deg,#bfe4f7,#2a9fd8)"></div></div>
    <div><h4>Mon, December. 28</h4><p>Lorem ipsum dolor sit amet, consectet adipiscing elit, sed diam nonummy nibh euismod tincidunt ut .</p></div>
  </div>
</section>

<section class="abs col testi">
  <div class="hatch"></div>
  <div class="col-head">
    <svg viewBox="0 0 28 28"><ellipse cx="14" cy="12" rx="12" ry="9" fill="#8a7f75"/><path d="M6 18 L4 26 L13 20z" fill="#8a7f75"/></svg>
    <h3>TESTIMONIALS</h3>
  </div>
  <div class="quote">
    <span class="mark">&ldquo;</span>
    <p>Duis autem vel eum iriure dolor in hendrerit in vulputate velit esse molestie consequat, vel illum dolore eu feugiat nulla facilisis at vero eros et accumsan et iusto odio.</p>
    <p>Nam liber tempor cum soluta nobis eleifend option congue nihil imperdiet doming id quod mazim placerat facer possim assum.</p>
    <p class="who">mr. Daro Lensi (manager)</p>
  </div>
</section>

<footer class="abs footer"><span>Copyright 2014. All rights reserved.</span><span>Privacy Policy | Terms of Use</span></footer>

</body>
</html>
```